Letterhead Design Project

Please do not submit designs until I upload file-

Project Deadline Extended

Requirements
Must have
• clean lines and font- easy to read; consistent with the design on the business card
Does not use too much of the real estate of the size of the paper

```html
<!DOCTYPE html>
<html lang="en">
<head>
<meta charset="utf-8">
<title>The Ridgeline Foundation – Letterhead</title>
<link href="https://fonts.googleapis.com/css2?family=Montserrat:wght@600&family=Didact+Gothic&display=swap" rel="stylesheet">
<style>
  :root {
    --backdrop: #e9eaeb;
    --paper: #ffffff;
    --navy: #1d3f6e;
    --slate: #6d7275;
    --ink: #3a3d40;
  }
  * { margin: 0; padding: 0; box-sizing: border-box; }
  html, body {
    width: 1200px;
    height: 795px;
    overflow: hidden;
    background: var(--backdrop);
  }
  .canvas {
    width: 1200px;
    height: 795px;
    display: flex;
    align-items: center;
    justify-content: center;
  }
  .letterhead {
    position: relative;
    width: 584px;
    height: 755px;
    background: var(--paper);
    box-shadow: 0 2px 10px rgba(0, 0, 0, 0.08);
  }
  .brand {
    position: absolute;
    top: 52px;
    left: 48px;
    display: flex;
    align-items: center;
    gap: 10px;
  }
  .brand-square {
    width: 26px;
    height: 26px;
    background: var(--navy);
  }
  .brand-name {
    font-family: "Montserrat", sans-serif;
    font-weight: 600;
    font-size: 11px;
    line-height: 1.05;
    letter-spacing: 0.04em;
    text-transform: uppercase;
    color: var(--navy);
  }
  .brand-tagline {
    display: block;
    margin-top: 3px;
    font-family: "Didact Gothic", sans-serif;
    font-size: 5px;
    letter-spacing: 0.1em;
    color: var(--slate);
  }
  .contact {
    position: absolute;
    left: 48px;
    bottom: 46px;
    font-family: "Didact Gothic", sans-serif;
    font-size: 8px;
    line-height: 1.9;
    letter-spacing: 0.06em;
    color: var(--ink);
    list-style: none;
  }
  .contact-address { margin-bottom: 8px; }
  .contact-line {
    display: flex;
    align-items: center;
    gap: 8px;
  }
  .contact-icon {
    width: 8px;
    height: 8px;
    flex: none;
  }
</style>
</head>
<body>
<main class="canvas">
  <article class="letterhead">
    <header class="brand">
      <span class="brand-square"></span>
      <p class="brand-name">The Ridgeline<br>Foundation<span class="brand-tagline">Giving Back Together</span></p>
    </header>

    <footer>
      <ul class="contact">
        <li class="contact-address">4180 Harbor Crest Ave. Suite 305<br>Palm Meadow, FL 33010</li>
        <li class="contact-line">
          <svg class="contact-icon" viewBox="0 0 8 8" aria-hidden="true">
            <rect x="2" y="0.5" width="4" height="7" rx="0.8" fill="none" stroke="#1d3f6e" stroke-width="1"/>
          </svg>
          +1-555-014-2268
        </li>
        <li class="contact-line">
          <svg class="contact-icon" viewBox="0 0 8 8" aria-hidden="true">
            <rect x="0.5" y="1.5" width="7" height="5" fill="none" stroke="#1d3f6e" stroke-width="1"/>
            <path d="M0.5 1.5 L4 4.5 L7.5 1.5" fill="none" stroke="#1d3f6e" stroke-width="1"/>
          </svg>
          clara.hayes@ridgelinefoundation.org
        </li>
        <li class="contact-line">
          <svg class="contact-icon" viewBox="0 0 8 8" aria-hidden="true">
            <circle cx="4" cy="4" r="3.4" fill="none" stroke="#1d3f6e" stroke-width="1"/>
            <path d="M0.6 4 H7.4 M4 0.6 C2.4 2.5 2.4 5.5 4 7.4 M4 0.6 C5.6 2.5 5.6 5.5 4 7.4" fill="none" stroke="#1d3f6e" stroke-width="0.7"/>
          </svg>
          www.ridgelinefoundation.org
        </li>
      </ul>
    </footer>
  </article>
</main>
</body>
</html>
```